Private chef located in Vail, CO

I would like my info located at the top of the landing page, perhaps some Vail mountain landscapes that I could swap out from summer to winter photos. I need the menu bar to have a link to a blog, about me, photo gallery, recipes & beer reviews. I would also like to have a shop, but only populated with products from corvelle or other online retailers that I can affiliate with.
Extremely wealthy, affluent people, concierge, international
5+ page

```html
<!DOCTYPE html>
<html lang="en">
<head>
<meta charset="utf-8">
<title>Chef Daniel Whitford – Private Chef in Vail</title>
<link href="https://fonts.googleapis.com/css2?family=Playfair+Display:wght@400;700&family=Open+Sans:wght@300;400;600&display=swap" rel="stylesheet">
<style>
  :root {
    --ink: #111111;
    --nav: #555555;
    --accent: #ea5a34;
    --white: #ffffff;
    --panel: #f1f1f1;
    --text: #2a2a2a;
    --footer: #2b2b2b;
    --footer-text: #c9c9c9;
    --icon: #6d6d6d;
    --star: #f5b800;
  }
  * { margin: 0; padding: 0; box-sizing: border-box; }
  html, body { width: 1200px; height: 990px; overflow: hidden; background: var(--white); }
  body { position: relative; font-family: "Open Sans", sans-serif; color: var(--text); }

  .site-header { position: absolute; left: 0; top: 0; width: 1200px; height: 98px; background: var(--white); }
  .brand { position: absolute; left: 144px; top: 14px; font-family: "Playfair Display", serif; font-weight: 700; font-size: 41px; color: var(--ink); letter-spacing: -0.5px; }
  .main-nav { position: absolute; right: 145px; top: 43px; display: flex; gap: 29px; font-weight: 300; font-size: 13px; color: var(--nav); }
  .main-nav .active { color: var(--accent); }

  .hero { position: absolute; left: 0; top: 98px; width: 1200px; height: 516px; overflow: hidden; }
  .hero-scene { position: absolute; inset: 0;
    background: linear-gradient(180deg, #2d5a86 0%, #5a7fa3 14%, #8a93a0 24%, #4d6e3a 38%, #3f6a2c 60%, #4a5a38 78%, #6b5a4a 100%); }
  .hero-shade { position: absolute; inset: 0; background: rgba(10, 25, 40, 0.18); }
  .chef-portrait { position: absolute; left: 310px; top: 138px; width: 200px; height: 200px; border-radius: 50%;
    background: radial-gradient(circle at 45% 40%, #b98c6e 0%, #5a4638 55%, #1e1e22 100%); border: 4px solid rgba(90,120,80,0.7); }
  .hero-title { position: absolute; left: 541px; top: 136px; font-family: "Playfair Display", serif; font-weight: 700; font-size: 45px; color: var(--white); letter-spacing: -0.5px; }
  .hero-sub { position: absolute; left: 546px; top: 192px; font-size: 24px; color: var(--white); }
  .rating { position: absolute; left: 545px; top: 242px; display: flex; align-items: center; gap: 11px; }
  .rating svg { width: 19px; height: 19px; }
  .rating-text { margin-left: 6px; font-size: 13px; font-weight: 600; color: var(--white); }
  .book-btn { position: absolute; left: 546px; top: 290px; width: 112px; height: 44px; background: var(--white); border-radius: 2px;
    font-family: "Playfair Display", serif; font-size: 17px; color: #333; display: flex; align-items: center; justify-content: center; }
  .slide-arrow { position: absolute; top: 244px; width: 29px; height: 27px; background: rgba(0,0,0,0.55); display: flex; align-items: center; justify-content: center; }
  .slide-arrow.prev { left: 0; }
  .slide-arrow.next { right: 0; }

  .contact { position: absolute; left: 0; top: 614px; width: 1200px; height: 273px; background: var(--panel); text-align: center; }
  .contact-title { position: absolute; left: 0; right: 0; top: 58px; font-family: "Playfair Display", serif; font-weight: 700; font-size: 44px; color: var(--accent); }
  .contact-line { position: absolute; left: 0; right: 0; top: 124px; font-size: 15.5px; color: var(--text); }
  .contact-line .sep { margin: 0 14px; }
  .social { position: absolute; left: 525px; top: 166px; display: flex; gap: 12px; }
  .social span { width: 28px; height: 28px; border-radius: 50%; background: var(--icon); display: block; }

  .site-footer { position: absolute; left: 0; top: 887px; width: 1200px; height: 103px; background: var(--footer); color: var(--footer-text); }
  .footer-nav { position: absolute; left: 144px; top: 26px; font-size: 12.5px; }
  .footer-nav .sep { margin: 0 9px; }
  .copyright { position: absolute; left: 144px; top: 58px; font-size: 12.5px; }
  .payments { position: absolute; right: 145px; top: 44px; display: flex; align-items: center; gap: 14px; font-size: 11px; font-weight: 400; color: var(--footer-text); }
  .payments .pay { display: flex; align-items: center; gap: 5px; }
  .payments .pay::before { content: ""; width: 7px; height: 7px; background: var(--footer-text); display: block; }
</style>
</head>
<body>
  <header class="site-header">
    <div class="brand">Daniel Whitford</div>
    <nav class="main-nav">
      <span class="active">Home</span><span>Blog</span><span>About Me</span><span>Photo Gallery</span><span>Recipes &amp; Beer Reviews</span><span>Contact Us</span>
    </nav>
  </header>

  <section class="hero">
    <div class="hero-scene" role="img" aria-label="Summer landscape of Vail valley with snowy peaks, green slopes and the village below"></div>
    <div class="hero-shade"></div>
    <div class="chef-portrait" role="img" aria-label="Portrait photo of the chef"></div>
    <h1 class="hero-title">Chef Daniel Whitford</h1>
    <p class="hero-sub">Private Chef In Vail</p>
    <div class="rating">
      <svg viewBox="0 0 24 24"><path fill="var(--star)" d="M12 1l3.4 7 7.6 1-5.5 5.3 1.3 7.6L12 18.3 5.2 21.9l1.3-7.6L1 9l7.6-1z"/></svg>
      <svg viewBox="0 0 24 24"><path fill="var(--star)" d="M12 1l3.4 7 7.6 1-5.5 5.3 1.3 7.6L12 18.3 5.2 21.9l1.3-7.6L1 9l7.6-1z"/></svg>
      <svg viewBox="0 0 24 24"><path fill="var(--star)" d="M12 1l3.4 7 7.6 1-5.5 5.3 1.3 7.6L12 18.3 5.2 21.9l1.3-7.6L1 9l7.6-1z"/></svg>
      <svg viewBox="0 0 24 24"><path fill="var(--star)" d="M12 1l3.4 7 7.6 1-5.5 5.3 1.3 7.6L12 18.3 5.2 21.9l1.3-7.6L1 9l7.6-1z"/></svg>
      <svg viewBox="0 0 24 24"><path fill="var(--star)" d="M12 1l3.4 7 7.6 1-5.5 5.3 1.3 7.6L12 18.3 5.2 21.9l1.3-7.6L1 9l7.6-1z"/></svg>
      <span class="rating-text">5|2 Reviews</span>
    </div>
    <div class="book-btn">Book Now</div>
    <div class="slide-arrow prev"><svg width="14" height="12" viewBox="0 0 14 12"><path d="M13 6H2M6 1L1 6l5 5" stroke="#fff" stroke-width="2.4" fill="none"/></svg></div>
    <div class="slide-arrow next"><svg width="14" height="12" viewBox="0 0 14 12"><path d="M1 6h11M8 1l5 5-5 5" stroke="#fff" stroke-width="2.4" fill="none"/></svg></div>
  </section>

  <section class="contact">
    <h2 class="contact-title">Let’s Talk</h2>
    <p class="contact-line">Phone: +34 611 45 27 03<span class="sep">|</span>Whatsapp: +34 611 45 27 03<span class="sep">|</span>E-mail: hello@alpinetable.com</p>
    <div class="social" aria-label="Social links"><span></span><span></span><span></span><span></span></div>
  </section>

  <footer class="site-footer">
    <div class="footer-nav">Home<span class="sep">|</span>Blog<span class="sep">|</span>About Me<span class="sep">|</span>Photo Gallery<span class="sep">|</span>Recipes &amp; Beer Reviews<span class="sep">|</span>Contact Us</div>
    <div class="copyright">Copyright © 2019 Daniel Whitford. All rights reserved.</div>
    <div class="payments" aria-label="Accepted payments">
      <span class="pay">Quillet</span><span class="pay">Brenmoor</span><span class="pay">Orvik</span><span class="pay">Tessal</span><span class="pay">Halden</span>
    </div>
  </footer>
</body>
</html>
```